International business needs business cards

Our company, DRV Ventures Inc. is in the business of supplying a range construction products with particular emphasis on CEMENT. We have developed our own brand - TORVAN SUPPLIES - with which to infiltrate the market. We are launching our brand of cement (TORVAN Type IS Cement) into the Caribbean which is unlike anything this market has ever seen. A monopoly has existed here for the past 60-odd years and the market has now opened to allow the importation of other brands and consumers are anxious and ready for change/improvement. We are very excited to be launching and want to make a great first impression. We will be conducting workshops and seminars (from government level to the hardware store owners) and we want our business card to give us the strong, confident introduction that we need.

Target Market(s)

construction; builders; engineers; home owners

Industry/Entity Type

Construction

Contact Information for Business Card

Marisol Depree
CEO
cell # 1 555 4180736
Ground floor,Lindell Plaza Suite 2734
George Town,Grand Cayman
Cayman Islands,KY1-4823
EMAIL: m.depree@drvventuresinc.example
web site drvventuresinc.example

COMPANY: skype info drv.ventures.example

second card
Yvette Brannock-Depree
CFO
CELL# 1 555 607 3941
George Town,Grand Cayman
Cayman Islands,KY1-4823
EMAIL: y.brannockdepree@drvventuresinc.example
website drvventuresinc.example

Requirements
Must have
• Business cards must display BOTH logos - DRV is the company and TORVAN is the brand.

```html
<!DOCTYPE html>
<html lang="en">
<head>
<meta charset="utf-8">
<title>DRV Ventures Inc. — Business Card</title>
<link rel="stylesheet" href="https://fonts.googleapis.com/css2?family=PT+Sans:wght@400;700&display=swap">
<style>
  :root {
    --page-bg: #e9e7e4;
    --card-black: #141414;
    --card-edge: #262626;
    --text-light: #e6e6e6;
    --text-muted: #bdbdbd;
    --accent-red: #b3161c;
    --mark-white: #f2f2f2;
    --divider: #8a8a8a;
  }
  * { box-sizing: border-box; margin: 0; padding: 0; }
  html, body {
    width: 1200px; height: 814px; overflow: hidden;
    background: var(--page-bg);
    font-family: "PT Sans", sans-serif;
  }
  .canvas {
    position: relative; width: 1200px; height: 814px;
    display: flex; align-items: center; justify-content: center; gap: 60px;
  }
  .card {
    width: 520px; height: 300px;
    background: var(--card-black);
    border: 1px solid var(--card-edge);
    box-shadow: 0 10px 28px rgba(0,0,0,.25);
    position: relative;
  }
  /* Contact side */
  .card-contact { display: flex; align-items: center; }
  .brand-block {
    width: 215px; height: 100%;
    display: flex; flex-direction: column; align-items: center; justify-content: center; gap: 12px;
  }
  .brand-square {
    width: 62px; height: 62px; background: #5a5a5a;
  }
  .brand-name {
    color: var(--text-light); font-size: 22px; font-weight: 700; letter-spacing: 4px;
  }
  .divider {
    width: 1px; height: 200px; background: var(--divider);
  }
  .details {
    padding-left: 22px; color: var(--text-light); font-size: 14px; line-height: 1.38;
  }
  .person-name { color: var(--accent-red); font-size: 19px; font-weight: 700; line-height: 1.2; }
  .person-role { margin-bottom: 6px; }
  .address { margin-bottom: 10px; }
  .contact-line { display: flex; align-items: center; gap: 8px; }
  .contact-line svg { width: 13px; height: 13px; flex: none; }
  /* Logo side */
  .card-front {
    display: flex; flex-direction: column; align-items: center; justify-content: center;
  }
  .company-mark { display: flex; align-items: center; gap: 14px; }
  .mark-square { width: 92px; height: 92px; background: var(--mark-white); }
  .company-name { display: flex; flex-direction: column; color: #cfcfcf; font-weight: 700; }
  .company-name .primary { font-size: 58px; line-height: .95; letter-spacing: 1px; }
  .company-name .secondary { font-size: 20px; letter-spacing: 1px; }
  .web-address {
    margin-top: 48px; color: var(--text-muted); font-size: 12px; letter-spacing: 3px;
  }
</style>
</head>
<body>
<main class="canvas">
  <section class="card card-contact" aria-label="Business card, contact side">
    <div class="brand-block">
      <div class="brand-square"></div>
      <div class="brand-name">TORVAN</div>
    </div>
    <div class="divider"></div>
    <div class="details">
      <p class="person-name">Marisol Depree</p>
      <p class="person-role">CEO</p>
      <p class="address">Ground floor<br>Lindell Plaza Suite 2734<br>George Town,Grand Cayman<br>Cayman Islands,KY1-4823</p>
      <p class="contact-line">
        <svg viewBox="0 0 12 12"><rect x="2.5" y="0.5" width="7" height="11" rx="1.2" fill="none" stroke="var(--accent-red)" stroke-width="1.3"/><circle cx="6" cy="9.5" r=".8" fill="var(--accent-red)"/></svg>
        1 555 4180736
      </p>
      <p class="contact-line">
        <svg viewBox="0 0 12 12"><rect x="0.5" y="2" width="11" height="8" fill="var(--accent-red)"/><path d="M0.5 2 L6 6.5 L11.5 2" fill="none" stroke="var(--card-black)" stroke-width="1"/></svg>
        m.depree@drvventuresinc.example
      </p>
      <p class="contact-line">
        <svg viewBox="0 0 12 12"><circle cx="6" cy="6" r="5.5" fill="var(--accent-red)"/><path d="M0.5 6 H11.5 M6 0.5 C3 3.5 3 8.5 6 11.5 M6 0.5 C9 3.5 9 8.5 6 11.5" fill="none" stroke="var(--card-black)" stroke-width=".8"/></svg>
        drvventuresinc.example
      </p>
    </div>
  </section>

  <section class="card card-front" aria-label="Business card, company side">
    <div class="company-mark">
      <div class="mark-square"></div>
      <div class="company-name">
        <span class="primary">DRV</span>
        <span class="secondary">VENTURES INC.</span>
      </div>
    </div>
    <p class="web-address">www.drvventuresinc.example</p>
  </section>
</main>
</body>
</html>
```